Web Design

We need a website for a company based in Doha Qatar called
Lumara Maid Service.

It is the number one maid cleaning service company, and we have branches all over qatar.

Luxury Cleaning Service Provider.

The color scheme is gold, yellow and black like the logo.

Before they get to the website, there is an intro video.

The website should depict luxury.

Target Market(s)

People who need maids at their houses.

Industry/Entity Type

Cleaning Service

Requirements
Must have
• Luxury, Sleek, Modern

The opening sequence is a video which I already have. Its too big to upload here so I am going to put it on youtube.

After the opening sequence, the home page should have a widescreen photo background and it should change every five seconds, the first background photo should be of qatar westbay skyline. Then the second background should be of maid photos in cleaning positions. Then the third background should be of cleaner photos etc.

We will send you all the tabs and all the content later.

```html
<!DOCTYPE html>
<html lang="en">
<head>
<meta charset="utf-8">
<title>Lumara Maid Service</title>
<link href="https://fonts.googleapis.com/css2?family=Josefin+Sans:wght@400;600;700&display=swap" rel="stylesheet">
<style>
  :root{
    --gold:#ffd400;
    --brand-gold:#d9a84a;
    --nav-text:#c9c9c9;
    --light:#dcdcdc;
    --header-bg:rgba(20,20,20,0.72);
    --footer-bg:#000;
    --footer-text:#cfcfcf;
    --circle-line:#8a8a8a;
    --sky:#8f9aa8;
    --glass:#5d6670;
    --shadow:#15171a;
  }
  *{margin:0;padding:0;box-sizing:border-box}
  html,body{width:1200px;height:761px;overflow:hidden;background:#111}
  body{font-family:"Josefin Sans",sans-serif;position:relative}

  .hero-photo{
    position:absolute;left:0;top:0;width:1200px;height:687px;
    background:
      radial-gradient(ellipse 420px 260px at 18% 22%, rgba(180,190,205,0.55), transparent 70%),
      radial-gradient(ellipse 520px 300px at 82% 28%, rgba(170,182,196,0.5), transparent 70%),
      radial-gradient(ellipse 520px 420px at 25% 70%, rgba(10,10,12,0.85), transparent 70%),
      radial-gradient(ellipse 560px 260px at 78% 82%, rgba(120,128,136,0.45), transparent 70%),
      linear-gradient(170deg,var(--sky) 0%,var(--glass) 35%,#33383e 65%,var(--shadow) 100%);
  }
  .hero-photo::after{content:"";position:absolute;inset:0;background:rgba(0,0,0,0.42)}

  .site-header{
    position:absolute;left:0;top:0;width:1200px;height:107px;
    background:var(--header-bg);
    border-bottom:1px solid rgba(255,255,255,0.06);
  }
  .brand{
    position:absolute;left:134px;top:38px;display:flex;align-items:center;gap:10px;
    color:var(--brand-gold);font-weight:600;font-size:17px;letter-spacing:1px;text-transform:uppercase;
  }
  .brand-dot{width:26px;height:26px;border-radius:50%;background:var(--brand-gold)}
  .main-nav a{
    position:absolute;top:47px;color:var(--nav-text);text-decoration:none;
    font-size:13px;font-weight:600;text-transform:uppercase;
  }

  .hero-title{
    position:absolute;left:0;top:263px;width:1200px;text-align:center;
    font-size:56px;font-weight:400;color:var(--light);text-transform:uppercase;line-height:1;
  }
  .hero-title strong{color:var(--gold);font-weight:700}

  .play-button{position:absolute;left:560px;top:412px}

  .site-footer{
    position:absolute;left:0;top:687px;width:1200px;height:74px;background:var(--footer-bg);
  }
  .copyright{
    position:absolute;left:131px;top:36px;color:var(--footer-text);
    font-size:10.5px;text-transform:uppercase;
  }
  .copyright span{margin-left:5px}
  .social{position:absolute;left:942px;top:27px;display:flex;gap:5px}
  .social i{
    width:28px;height:28px;border-radius:50%;border:2px solid var(--circle-line);
    display:flex;align-items:center;justify-content:center;
  }
  .social i::before{content:"";width:6px;height:6px;border-radius:50%;background:var(--circle-line)}
  .social i.active{border-color:var(--gold)}
  .social i.active::before{background:var(--gold)}
</style>
</head>
<body>
  <div class="hero-photo" role="img" aria-label="Widescreen photo of a cleaner washing a large glass window under a cloudy sky"></div>

  <header class="site-header">
    <div class="brand"><span class="brand-dot"></span>Lumara Maid Service</div>
    <nav class="main-nav">
      <a href="#" style="left:472px">Home</a>
      <a href="#" style="left:564px">About Us</a>
      <a href="#" style="left:679px">Services</a>
      <a href="#" style="left:786px">Our Staff</a>
      <a href="#" style="left:911px">Blog</a>
      <a href="#" style="left:996px">Contacts</a>
    </nav>
  </header>

  <h1 class="hero-title"><strong>Lumara</strong> Maid Service</h1>

  <svg class="play-button" width="80" height="80" viewBox="0 0 82 82" aria-label="Play video">
    <circle cx="41" cy="41" r="39.5" fill="rgba(15,15,15,0.85)" stroke="#bdbdbd" stroke-width="2"/>
    <path d="M30 25 L57 41 L30 57 Z" fill="#fff"/>
  </svg>

  <footer class="site-footer">
    <p class="copyright">Lumara Maid Service © 2014 All Rights Reserved <span>Privacy Policy</span></p>
    <div class="social" aria-label="Social links"><i></i><i class="active"></i><i></i><i></i></div>
  </footer>
</body>
</html>
```